Velvet Moon Wheel Method Needs a Website

I require a Wordpress website so that I can do simple edits myself. I want it to be a fairly simple design as the videos and the text will speak for themselves.
The concept is simple, we have developed a revolutionary roulette system that proves the game is NOT random. This breakthrough is absolutely massive. We are offering a 12-part training course to take a beginner to a professional at their own pace through watching videos made by our roulette genius.
Roulette and casinos have a glitzy feel about them and this should be reflected in the style of the site. The roulette wheel, table and chips are very evocative and pictures of these would be good.
There is a home page and 5 other pages containing sub-pages. These should be interlinked and it must be easy to get back to the home page from anywhere on the site.
Coinvey links should appear at the bottom of each page.
I really need the site in a hurry as we were let down badly by the last developer we hired who went on holiday and left us in the lurch.

Target Market(s)

Gamblers, betting community, opportunity seekers

Coding

Coded - Design and coding required

Number of Pages Required

1 page

Font styles to use
Sans Serif

Requirements
Must have
• At least two videos on the Home page.
• Coinvey details on every page and tab.
• A box for name and email address for interested parties to leave their details.

```html
<!DOCTYPE html>
<html lang="en">
<head>
<meta charset="utf-8">
<title>Velvet Moon Wheel Method</title>
<link href="https://fonts.googleapis.com/css2?family=Roboto:wght@300;400;500;700&display=swap" rel="stylesheet">
<style>
:root{
  --red:#e8141b;
  --red-dark:#c40d12;
  --ink:#1b1b1b;
  --navy:#1b2128;
  --side:#1e252d;
  --gold:#b08a3a;
  --green:#2b8a4a;
  --grey-bg:#f4f4f4;
  --text:#555;
  --footer:#252525;
  --footer-base:#151515;
}
*{box-sizing:border-box;margin:0;padding:0}
html,body{width:675px;height:1200px;overflow:hidden}
body{font-family:'Roboto',sans-serif;color:var(--ink);background:#fff;position:relative}
.abs{position:absolute}

/* header / sidebar */
.sidebar{left:0;top:0;width:129px;height:304px;background:var(--side)}
.topbar{left:0;top:0;width:129px;height:19px;background:#11161b;color:#ccc;font-size:5.6px;display:flex;align-items:center;gap:5px;padding-left:5px;white-space:nowrap}
.topbar svg{width:5px;height:5px;fill:#ccc;vertical-align:middle;margin-right:1px}
.brand{left:0;top:19px;width:129px;height:48px;background:#151a20;display:flex;align-items:center;justify-content:center;color:var(--red);font-size:9px;font-weight:400;white-space:nowrap}
.nav{left:0;top:67px;width:129px;list-style:none}
.nav li{height:29px;display:flex;align-items:center;justify-content:center;font-size:7px;color:#55606b;border-bottom:1px solid #27303a;margin:0 12px}
.nav li.active{color:#fff}
.hero{left:129px;top:0;width:546px;height:304px;background:radial-gradient(circle at 80% 35%,#c4425a 0%,#6a2a52 22%,#1d2a58 50%,#0a0f22 85%)}
.hero-title{left:165px;top:158px;color:#fff;font-size:24px;font-weight:500}
.hero-sub{left:165px;top:194px;width:300px;color:#fff;font-size:11.5px;line-height:19px}
.arrows{left:165px;top:250px;display:flex;gap:1px}
.arrows span{width:17px;height:17px;background:#1a1d22;color:#fff;font-size:9px;display:flex;align-items:center;justify-content:center}
.arrows span:first-child{background:#888}

/* welcome */
.section-title{width:675px;left:0;text-align:center;font-size:13px;font-weight:500}
.section-title em{font-style:normal;color:var(--red)}
.lede{left:130px;width:415px;text-align:center;font-size:6.6px;line-height:12.6px;color:var(--text)}
.btn{display:inline-flex;align-items:center;justify-content:center;font-size:7.5px;color:#fff;border-radius:3px}
.btn-red{background:linear-gradient(#f22,#c40d12)}
.btn-dark{background:linear-gradient(#2b333b,#12171c)}

/* training */
.training{left:0;top:484px;width:675px;height:164px;background:var(--grey-bg)}
.band{left:0;top:648px;width:675px;height:152px;background:linear-gradient(90deg,#1a2433,#2a3342 50%,#1a2433)}
.card{width:134px;top:583px}
.card-head{height:29px;display:flex;align-items:center;justify-content:center;color:#fff;font-size:8.6px;font-weight:500}
.card-body{height:36px;color:#fff;font-size:6px;font-weight:300;line-height:12.6px;text-align:center;padding:5px 8px 0}
.card-photo{height:109px}
.card .more{position:absolute;top:163px;left:50%;transform:translateX(-50%);width:53px;height:20px;border:1px solid #fff;border-radius:3px;font-size:6.6px;color:#fff;display:flex;align-items:center;justify-content:center}
.c-red .card-head{background:var(--red)} .c-red .card-body{background:#b40f14} .c-red .more{background:var(--red)}
.c-dark .card-head{background:#25292e} .c-dark .card-body{background:#171a1d} .c-dark .more{background:#2a2e33}
.c-gold .card-head{background:#b8944a} .c-gold .card-body{background:#8a6a2a} .c-gold .more{background:#a7853b}
.c-green .card-head{background:#2f9a50} .c-green .card-body{background:#1f6e38} .c-green .more{background:#2a8a47}

/* pricing */
.pricing{left:0;top:800px;width:675px;height:226px;background:var(--grey-bg)}
.plan-intro{left:55px;top:866px;font-size:18px;line-height:27px;font-weight:400}
.plan-rule{left:55px;top:932px;width:49px;height:1px;background:var(--red)}
.plan-link{left:55px;top:950px;color:var(--red);font-size:8.5px}
.divider{left:199px;top:820px;width:4px;height:180px;background:linear-gradient(90deg,rgba(0,0,0,.12),transparent)}
.plan{top:826px;width:216px;height:171px;padding:16px 21px}
.plan h3{font-size:14.5px;font-weight:700;line-height:18px}
.plan .price{font-size:9px;margin-top:3px}
.plan p{font-size:6.4px;line-height:12.6px;margin-top:12px}
.plan .btn{margin-top:12px;width:56px;height:20px;font-size:6.8px}
.plan-grey{left:212px;background:linear-gradient(#dcdcdc,#f3f3f3)}
.plan-grey h3,.plan-grey .price{color:var(--red)}
.plan-grey p{color:#666}
.plan-red{left:449px;background:var(--red);color:#fff;box-shadow:0 0 0 1px #d0d0d0}
.plan-red .btn{background:#1e252d;border:1px solid #fff}

/* footer */
.footer{left:0;top:1026px;width:675px;height:144px;background:var(--footer);color:#aaa}
.fcol{top:1047px}
.fcol h4{color:#fff;font-size:9.5px;font-weight:500;letter-spacing:.5px;margin-bottom:11px}
.fcol ul{list-style:none}
.fcol li{font-size:6.5px;line-height:16.8px;color:#aaa}
.contact li{display:flex;gap:7px;align-items:flex-start;line-height:11px;margin-bottom:6px}
.contact svg{width:6px;height:6px;fill:var(--red);flex:none;margin-top:2px}
.field{width:113px;height:19px;background:#fff;border-radius:3px;font-size:6.5px;color:#999;display:flex;align-items:center;padding-left:6px;margin-bottom:6px}
.newsletter .btn{width:43px;height:15px;font-size:5px;background:var(--red);border:1px solid #fff;border-radius:4px}
.copyright{left:0;top:1170px;width:675px;height:30px;background:var(--footer-base);color:#fff;font-size:6.6px;display:flex;align-items:center;justify-content:center}
</style>
</head>
<body>

<div class="abs hero" role="img" aria-label="Close-up photograph of a spinning roulette wheel in casino lights"></div>
<div class="abs sidebar"></div>
<div class="abs topbar">
  <span><svg viewBox="0 0 10 10"><path d="M2 0h2l1 3-1.5 1a6 6 0 0 0 2.5 2.5L7 5l3 1v2c0 1-1 2-2 2A8 8 0 0 1 0 2c0-1 1-2 2-2z"/></svg>010 555 01 23</span>
  <span><svg viewBox="0 0 10 8"><path d="M0 0h10v1L5 4 0 1zM0 2l5 3 5-3v6H0z"/></svg>sales@vmwm.example</span>
</div>
<div class="abs brand">Velvet Moon Wheel Method</div>
<ul class="abs nav">
  <li class="active">HOME</li><li>TRAINING</li><li>CASINOS</li><li>COACHING</li><li>OVERSEAS TRIP</li><li>FAQ</li><li>CONTACT US</li>
</ul>
<h1 class="abs hero-title">VELVET MOON WHEEL METHOD</h1>
<p class="abs hero-sub">We have developed a revolutionary roulette system that proves the game is NOT random.</p>
<div class="abs arrows"><span>‹</span><span>›</span></div>

<h2 class="abs section-title" style="top:331px">WELCOME TO <em>VELVET MOON WHEEL METHOD</em></h2>
<p class="abs lede" style="top:358px">The idea of the monthly membership is to release a new video every month which builds on what you've learned from the previous one. The ideal scenario is that you watch the first video as many times as you need to, until you fully understand the concept. You can then practise the techniques you've learned in 'fun mode' which nearly all casino sites will offer you. Once you have played at least 10 rounds of roulette in fun mode, made a profit each time without making any mistakes and are happy that you are playing correctly</p>
<div class="abs" style="left:228px;top:430px;display:flex;gap:9px">
  <span class="btn btn-red" style="width:110px;height:23px">MONTHLY MEMBERSHIP</span>
  <span class="btn btn-dark" style="width:101px;height:23px">COURSE DESCRIPTION</span>
</div>

<div class="abs training"></div>
<h2 class="abs section-title" style="top:509px">OUR <em>TRAINING</em></h2>
<p class="abs lede" style="top:536px">The idea of the monthly membership is to release a new video every month which builds on what you've learned from the previous one. The ideal scenario is that you watch the first video as many times as you need to, until you fully understand the concept.</p>
<div class="abs band" role="img" aria-label="Dim casino floor photograph behind the training cards"></div>

<div class="abs card c-red" style="left:55px">
  <div class="card-head">COURSE DESCRIPTION</div>
  <div class="card-body">It is a long established fact that a reader will be distracted by the readable</div>
  <div class="card-photo" role="img" aria-label="Roulette wheel with ball in motion" style="background:linear-gradient(135deg,#3c4a6a,#8c96b2 55%,#2a3350)"></div>
  <span class="more">READ MORE</span>
</div>
<div class="abs card c-dark" style="left:199px">
  <div class="card-head">MONTHLY MEMBERSHIP</div>
  <div class="card-body">It is a long established fact that a reader will be distracted by the readable</div>
  <div class="card-photo" role="img" aria-label="Group of friends playing at a roulette table" style="background:linear-gradient(135deg,#3a2a1c,#8a6a42 55%,#2a1e14)"></div>
  <span class="more">READ MORE</span>
</div>
<div class="abs card c-gold" style="left:342px">
  <div class="card-head">THE COMPLETE SYSTEM</div>
  <div class="card-body">It is a long established fact that a reader will be distracted by the readable</div>
  <div class="card-photo" role="img" aria-label="Excited player celebrating a win at a slot machine" style="background:linear-gradient(135deg,#1e3a6a,#c49a8a 55%,#3a2a4a)"></div>
  <span class="more">REDA MORE</span>
</div>
<div class="abs card c-green" style="left:486px">
  <div class="card-head">PROPERTY RIGHTS</div>
  <div class="card-body">It is a long established fact that a reader will be distracted by the readable</div>
  <div class="card-photo" role="img" aria-label="Confident gambler in sunglasses with casino chips" style="background:linear-gradient(135deg,#2a3038,#5a6068 55%,#1a1e24)"></div>
  <span class="more">READ MORE</span>
</div>

<div class="abs pricing"></div>
<div class="abs plan-intro">MONTHLY<br>SUBSCRIPTION</div>
<div class="abs plan-rule"></div>
<div class="abs plan-link">VIEW MORE</div>
<div class="abs divider"></div>
<div class="abs plan plan-grey">
  <h3>MONTHLY SUBSCRIPTION</h3>
  <div class="price">£100.00 / MONTH FOR 24 MONTHS</div>
  <p>The idea of the monthly membership is to release a new video every month which builds on what you've learned from the previous one. The ideal scenario is that you watch the first video as many times as you need to, until you fully understand the concept.</p>
  <span class="btn btn-red">SIGN UP NOW</span>
</div>
<div class="abs plan plan-red">
  <h3>SINGLE PAYMENT</h3>
  <div class="price">£1000.00 / ON THIME PAYMENT</div>
  <p>The idea of the monthly membership is to release a new video every month which builds on what you've learned from the previous one. The ideal scenario is that you watch the first video as many times as you need to, until you fully understand the concept.</p>
  <span class="btn">SIGN UP NOW</span>
</div>

<div class="abs footer"></div>
<div class="abs fcol contact" style="left:55px">
  <h4>CONTACT US</h4>
  <ul>
    <li><svg viewBox="0 0 10 10"><path d="M5 0a3.5 3.5 0 0 1 3.5 3.5C8.5 6 5 10 5 10S1.5 6 1.5 3.5A3.5 3.5 0 0 1 5 0z"/></svg><span>NW, East Harbourside<br>1234 12th Avenue</span></li>
    <li><svg viewBox="0 0 10 10"><path d="M2 0h2l1 3-1.5 1a6 6 0 0 0 2.5 2.5L7 5l3 1v2c0 1-1 2-2 2A8 8 0 0 1 0 2c0-1 1-2 2-2z"/></svg><span>Phone - 010 555 01 23</span></li>
    <li><svg viewBox="0 0 10 10"><path d="M2 0h6v3H2zM0 3h10v5H8v2H2V8H0z"/></svg><span>Fax - (425) 555-0148</span></li>
    <li><svg viewBox="0 0 10 8"><path d="M0 0h10v1L5 4 0 1zM0 2l5 3 5-3v6H0z"/></svg><span>E-mail - sales@vmwm.example</span></li>
  </ul>
</div>
<div class="abs fcol" style="left:198px">
  <h4>QUICK LINKS</h4>
  <ul><li>Home</li><li>Wheel Method Training</li><li>Casinos</li><li>Coaching</li><li>Las Vegas</li></ul>
</div>
<div class="abs fcol" style="left:302px">
  <h4>OUR POLICY</h4>
  <ul><li>Help &amp; Contact</li><li>Well Education</li><li>Casino</li><li>Affiliaties</li></ul>
</div>
<div class="abs fcol" style="left:405px;top:1049px">
  <h4>COMMUNITY</h4>
  <ul style="margin-top:-4px"><li>Guiglines</li><li>Terms &amp; conditions</li><li>privacy policy</li><li>site map</li><li>Contact us</li></ul>
</div>
<div class="abs fcol newsletter" style="left:507px;top:1049px">
  <h4>NEWSLETTER</h4>
  <div class="field">Name</div>
  <div class="field">Mail id</div>
  <span class="btn" style="margin-top:2px">SIGN UP NOW</span>
</div>
<div class="abs copyright">Copyrights@2016Compny name , All rights Reserved</div>

</body>
</html>
```